carpet bamboo timber flooring flyer EVERYONE NOTE WE SELL CARPET AND VINYL AS WELL PICTURES TBC

make a A4 Flyer to send to builder real estate companies customers insurance ect ect in the profession5 folder our logo is number 5
we are calling all builders ect in our area then following up with flyer at the same time to try to get projects or customers to quote on like flood damage rental properties new home builds , tenders ect

we will need to discuss with pictures go where ect but you have the idea what im after

Target Market(s)

builders insurance brokers customers builders developers

Industry/Entity Type

Flooring

Font styles to use
Decorative

Colors
f37122
fabb94
fee18a
faa54b

Requirements
Must have
• class clear vision high impact call to action informative
Nice to have
• like to see images on our showroom and recent jobs logos of our main brands

```html
<!DOCTYPE html>
<html lang="en">
<head>
<meta charset="utf-8">
<title>Summitline Floors – Tri-fold Brochure Inside Spread</title>
<link href="https://fonts.googleapis.com/css2?family=Open+Sans:wght@400;600;700&display=swap" rel="stylesheet">
<style>
  :root {
    --orange: #f37122;
    --orange-light: #faa54b;
    --orange-deep: #e85d12;
    --peach: #fabb94;
    --paper: #ffffff;
    --backdrop: #dcdcdc;
    --timber: #8a6444;
    --timber-dark: #5c3a22;
    --carpet-grey: #8d8d8f;
    --carpet-plum: #4a2232;
  }
  * { box-sizing: border-box; margin: 0; padding: 0; }
  html, body { width: 1200px; height: 870px; overflow: hidden; }
  body {
    background: var(--backdrop);
    font-family: "Open Sans", Arial, sans-serif;
    position: relative;
  }
  .spread {
    position: absolute; left: 30px; top: 35px;
    width: 1140px; height: 800px;
    background: var(--paper);
    box-shadow: 0 6px 18px rgba(0,0,0,.18);
  }
  /* Left information panel */
  .info-panel {
    position: absolute; left: 0; top: 0;
    width: 380px; height: 800px;
    background: linear-gradient(160deg, var(--orange) 0%, var(--orange-light) 100%);
    color: #fff;
    padding: 34px 30px 0 32px;
  }
  .info-panel h2 {
    font-size: 14px; font-weight: 700; letter-spacing: .3px;
    text-transform: uppercase;
    padding-bottom: 4px;
    border-bottom: 1px solid rgba(255,255,255,.85);
    margin-bottom: 8px;
  }
  .info-panel p {
    font-size: 11.6px; line-height: 1.42;
    text-align: justify; margin-bottom: 13px;
  }
  .info-section { margin-bottom: 26px; }
  .service-list { list-style: none; margin-top: -4px; }
  .service-list li {
    font-size: 11.6px; line-height: 1.5;
    display: flex; align-items: center; gap: 7px;
  }
  .service-list svg { flex: none; }
  .info-band {
    position: absolute; left: 0; bottom: 0; width: 380px; height: 58px;
  }
  /* Gallery panels */
  .photo {
    position: absolute;
  }
  .photo--living   { left: 392px; top: 12px; width: 508px; height: 353px;
    background: linear-gradient(170deg, #7d8a4a 0%, #6b5a48 35%, var(--timber) 60%, var(--timber-dark) 100%); }
  .photo--stools   { left: 912px; top: 12px; width: 216px; height: 473px;
    background: linear-gradient(180deg, #cfc7bd 0%, #9a7350 45%, var(--timber) 70%, #6e4a2e 100%); }
  .photo--fireplace{ left: 392px; top: 377px; width: 218px; height: 148px;
    background: linear-gradient(160deg, #e9e2d6 0%, #a66a45 55%, #6d2f1a 100%); }
  .photo--bedroom  { left: 392px; top: 537px; width: 218px; height: 193px;
    background: linear-gradient(175deg, #b9a48e 0%, #6b4c50 45%, var(--carpet-plum) 100%); }
  .photo--lounge   { left: 622px; top: 497px; width: 506px; height: 233px;
    background: linear-gradient(160deg, #c9ccce 0%, #9d9ea0 40%, var(--carpet-grey) 100%); }
  .tagline-box {
    position: absolute; left: 622px; top: 377px; width: 278px; height: 108px;
    background: var(--orange);
    color: #fff;
    display: flex; flex-direction: column; justify-content: center; align-items: center;
    font-size: 15px; font-weight: 600; letter-spacing: .4px; line-height: 1.35;
    text-transform: uppercase; text-align: center;
  }
  .footer-band {
    position: absolute; left: 392px; top: 745px; width: 748px; height: 26px;
    background: var(--orange);
    color: #fff; font-size: 13px; letter-spacing: .6px;
    display: flex; align-items: center; justify-content: flex-end;
    padding-right: 22px;
  }
  .fold {
    position: absolute; top: 0; width: 1px; height: 800px;
    background: rgba(0,0,0,.06);
  }
</style>
</head>
<body>
  <main class="spread">
    <section class="info-panel">
      <div class="info-section">
        <h2>About Us</h2>
        <p>Summitline Floors is the undisputed floorboards leader in Adelaide. Since our humble beginnings in 1980, we have earned ourselves a renowned reputation for delivering quality flooring solutions across Adelaide. We are committed to fulfilling the flooring needs of our valued customers. As a company we believe timber flooring is a great investment for your home as it outlasts other floors and offers a timeless and stylish look. Furthermore, it is highly durable and is easy to clean and maintain.</p>
        <p>The Summitline Floors team consists of industry professionals who are experts across a range of materials and designs, ensuring every customer receives the perfect floor.</p>
      </div>
      <div class="info-section">
        <h2>Floor Sanding &amp; Polishing</h2>
        <p>At Summitline Floors we provide an exceptional floor sanding and polishing service in Adelaide. We strive to provide a sanding and polishing solution for all types of timber flooring. Whether we have just installed your new timber flooring, or you want to refurbish your old, worn timber floor, we are the professionals for you.</p>
        <p>We can sand and polish the following flooring:</p>
        <ul class="service-list">
          <li><svg width="11" height="11" viewBox="0 0 12 12" aria-hidden="true"><circle cx="6" cy="6" r="5.2" fill="none" stroke="#fff" stroke-width="1"/><path d="M5 3.6 7.4 6 5 8.4" fill="none" stroke="#fff" stroke-width="1.3"/></svg>Floating timber floors</li>
          <li><svg width="11" height="11" viewBox="0 0 12 12" aria-hidden="true"><circle cx="6" cy="6" r="5.2" fill="none" stroke="#fff" stroke-width="1"/><path d="M5 3.6 7.4 6 5 8.4" fill="none" stroke="#fff" stroke-width="1.3"/></svg>Parquetry floors</li>
          <li><svg width="11" height="11" viewBox="0 0 12 12" aria-hidden="true"><circle cx="6" cy="6" r="5.2" fill="none" stroke="#fff" stroke-width="1"/><path d="M5 3.6 7.4 6 5 8.4" fill="none" stroke="#fff" stroke-width="1.3"/></svg>Cork tiles</li>
          <li><svg width="11" height="11" viewBox="0 0 12 12" aria-hidden="true"><circle cx="6" cy="6" r="5.2" fill="none" stroke="#fff" stroke-width="1"/><path d="M5 3.6 7.4 6 5 8.4" fill="none" stroke="#fff" stroke-width="1.3"/></svg>New and old flooring of all species</li>
        </ul>
      </div>
      <div class="info-section">
        <h2>Carpet and Vinyl</h2>
        <p>Carpet and Vinyl flooring can be a great option for your home or business. All it takes is a little bit of patience in finding the right type to suit any aesthetic.</p>
      </div>
      <svg class="info-band" viewBox="0 0 380 58" preserveAspectRatio="none" aria-hidden="true">
        <rect x="0" y="8" width="380" height="10" fill="#e8630f" opacity=".55"/>
        <rect x="0" y="24" width="380" height="34" fill="#e85d12"/>
      </svg>
    </section>

    <div class="photo photo--living" role="img" aria-label="Photo of an open living room with wide timber floorboards, lounge chairs and green curtains"></div>
    <div class="photo photo--stools" role="img" aria-label="Photo of bar stools standing on a polished timber floor"></div>
    <div class="photo photo--fireplace" role="img" aria-label="Photo of a room with a white fireplace and dark polished timber floor"></div>
    <div class="photo photo--bedroom" role="img" aria-label="Photo of a room with plum carpet, a white armchair and shuttered windows"></div>
    <div class="photo photo--lounge" role="img" aria-label="Photo of a modern lounge with patterned grey carpet and a glass coffee table"></div>

    <div class="tagline-box">
      <span>When quality value</span>
      <span>&amp; reliability counts</span>
    </div>

    <div class="footer-band">www.summitlinefloors.com.au</div>

    <span class="fold" style="left:380px"></span>
    <span class="fold" style="left:760px"></span>
  </main>
</body>
</html>
```